Oakmere Animal Care Group of Central Pennsylvania

I need a business card design for a new company in Harrisburg PA called "Animal Care Oakmere Group of Central PA". I will be providing relief services for veterinarians who need coverage during vacations; sick/maternity leave, etc. I would like to see the veterinarian symbol incorporated in the design in combination with animals (dogs /cats/birds/reptiles an pocket pets). Include My full name: Tomás R. Quintaval DVM, MLAS, BS. Also include my e mail (dvmtrq@mailbrook.net) and phone number 5552846017

Target Market(s)

Small Animal Veterinarian, practice owner

Industry/Entity Type

Business

Contact Information for Business Card

Oakmere Animal Care Group of Central PA

Font styles to use
Script

Requirements
Must have
• Veterinarian caduceus (see image) and Small animals (pets) within the logo.
Nice to have
• Give a sense of relaxation (vacationing)
Should not have
• Large animals, i.e. horses, cows, zoo animals...

```html
<!DOCTYPE html>
<html lang="en">
<head>
<meta charset="utf-8">
<title>Animal Care Oakmere Group of Central PA — Business Card</title>
<link rel="stylesheet" href="https://fonts.googleapis.com/css2?family=Cinzel:wght@600&family=Niconne&family=Sofia&display=swap">
<style>
  :root {
    --page-bg: #ecebe8;
    --card-bg: #fbfaf8;
    --ink: #1d1b1b;
    --accent-red: #b3262d;
    --photo-warm: #e9e1d4;
    --photo-soft: #f3efe8;
    --photo-grey: #e2e1df;
    --divider: #222;
  }
  * { box-sizing: border-box; margin: 0; padding: 0; }
  html, body {
    width: 1200px;
    height: 892px;
    overflow: hidden;
    background: var(--page-bg);
  }
  .canvas {
    position: relative;
    width: 1200px;
    height: 892px;
  }
  .card {
    position: absolute;
    left: 120px;
    top: 166px;
    width: 960px;
    height: 560px;
    border-radius: 34px;
    background: var(--card-bg);
    overflow: hidden;
    box-shadow: 0 10px 30px rgba(0,0,0,0.12);
  }
  .photo-dog {
    position: absolute;
    left: 380px;
    top: 0;
    width: 580px;
    height: 560px;
    background: radial-gradient(ellipse 60% 65% at 50% 35%, var(--photo-warm) 0%, var(--photo-soft) 55%, rgba(251,250,248,0) 100%);
  }
  .photo-paw {
    position: absolute;
    left: 0;
    top: 230px;
    width: 380px;
    height: 330px;
    background: radial-gradient(ellipse 50% 50% at 45% 60%, var(--photo-grey) 0%, rgba(251,250,248,0) 100%);
  }
  .brand {
    position: absolute;
    left: 30px;
    top: 140px;
    width: 420px;
    text-align: center;
  }
  .brand-circle {
    display: block;
    margin: 0 auto 18px;
  }
  .brand-name {
    font-family: "Cinzel", serif;
    font-weight: 600;
    font-size: 30px;
    line-height: 1.15;
    color: var(--ink);
    letter-spacing: 0.5px;
  }
  .divider {
    position: absolute;
    left: 470px;
    top: 100px;
    width: 2px;
    height: 330px;
    background: var(--divider);
  }
  .contact {
    position: absolute;
    left: 515px;
    top: 128px;
    width: 420px;
  }
  .person-name {
    font-family: "Niconne", cursive;
    font-size: 52px;
    line-height: 1.1;
    color: var(--accent-red);
    white-space: nowrap;
  }
  .person-credentials {
    font-family: "Sofia", cursive;
    font-size: 22px;
    color: var(--accent-red);
    margin: 4px 0 24px;
  }
  .contact-line {
    font-family: "Sofia", cursive;
    font-size: 26px;
    color: var(--ink);
    line-height: 1.7;
    white-space: nowrap;
  }
</style>
</head>
<body>
<div class="canvas">
  <div class="card">
    <div class="photo-paw" role="img" aria-label="Faint photo of a white kitten's paw"></div>
    <div class="photo-dog" role="img" aria-label="Faint photo of a puppy holding a stethoscope"></div>

    <div class="brand">
      <svg class="brand-circle" width="120" height="120" viewBox="0 0 120 120" aria-hidden="true">
        <circle cx="60" cy="60" r="52" fill="none" stroke="var(--accent-red)" stroke-width="8"/>
      </svg>
      <p class="brand-name">Animal Care Oakmere<br>Group of Central PA</p>
    </div>

    <div class="divider"></div>

    <div class="contact">
      <p class="person-name">Tomás R. Quintaval</p>
      <p class="person-credentials">DVM, MLAS, BS</p>
      <p class="contact-line">5552846017</p>
      <p class="contact-line">dvmtrq@mailbrook.net</p>
    </div>
  </div>
</div>
</body>
</html>
```